QP Fiduciary Website Redesign Contest

We want to refresh our website to be more insitutional, professional for an international audience. We have designed a new logo for this purpose and that has been attached. A full brand brief and positioning statement has also been attached. Please read through all the documents carefully before designing. The old website is found here: https://qp-fiduciary.example/

Target Market(s)

Actuaries and associated businesses internationally

Industry/Entity Type

professional services - actuaries

Number of Pages Required

3 page

Font styles to use
Sans Serif

Colors
0054AA
0677BA
7BADD7
CADEEF
E8F1F8
0094D4
00A9DD
6FCCEA
C7EBF8
E9F6FB
F0912C
F2A743
F7CA91
FBE8D2
FDF5EE
EE7325
F08F49
F5BC92
FAE3D3
FDF4ED
EB3D1F
EC4F4E
F09395
F8D3D4
FCEDEE

Requirements
Must have
• blues and greens to match the logo color, complimentary colors, navigation
Nice to have
• old site: https://qp-fiduciary.example/

```html
<!DOCTYPE html>
<html lang="en">
<head>
<meta charset="utf-8">
<title>QP Fiduciary — Actuarial Software</title>
<link href="https://fonts.googleapis.com/css2?family=Jura:wght@500;600&family=Lato:ital,wght@0,400;0,700;1,400&display=swap" rel="stylesheet">
<style>
:root{
  --blue:#0054AA;--blue2:#0677BA;--sky:#7BADD7;--pale:#E8F1F8;--tint:#eef6fb;
  --teal:#0a9e86;--orange:#F57A12;--ink:#111;--body:#444;--line:#dfe6ee;
}
*{box-sizing:border-box;margin:0;padding:0}
html,body{width:1200px;height:3854px;overflow:hidden;background:#fff}
body{font-family:"Lato",sans-serif;color:var(--ink);position:relative}
.h{font-family:"Jura",sans-serif;font-weight:600}
section,header,footer{position:absolute;left:0;width:1200px}
.abs{position:absolute}
.center{text-align:center;left:0;width:1200px}
.label{font-family:"Jura",sans-serif;font-weight:600;font-size:16px;letter-spacing:1px;color:var(--blue)}
.title{font-size:32px;color:#111}
.btn{display:flex;align-items:center;justify-content:center;background:var(--orange);color:#fff;font-weight:700;font-size:16px;border-radius:24px;height:46px}
.site-header{top:0;height:85px;background:#fff}
.brand{left:108px;top:22px;font-family:"Jura",sans-serif;font-weight:600;font-size:34px;color:var(--blue);letter-spacing:1px;display:flex;align-items:center;gap:10px}
.brand i{width:14px;height:14px;background:var(--orange);border-radius:50%;display:block}
.nav{left:540px;top:32px;display:flex;gap:30px;font-size:15px;color:#222}
.nav .on{color:var(--blue);text-decoration:underline}
.hero{top:85px;height:600px;background:linear-gradient(180deg,#dbe6f1 0%,#eef3f8 45%,#d7e2ee 100%)}
.hero-art{left:240px;top:270px;width:720px;height:310px;border-radius:50%;background:radial-gradient(ellipse at center,#f7f9fc 0%,#c6d4e4 60%,rgba(200,215,230,0) 75%)}
.hero h1{top:62px;font-size:41px;line-height:60px;color:var(--blue);letter-spacing:2px;font-weight:600}
.hero p{top:198px;font-size:16px;line-height:26px;color:#222}
.overview{top:685px;height:610px}
.overview p{left:110px;top:230px;width:446px;font-size:14px;line-height:26px;color:var(--body);text-align:justify}
.ov-img{left:628px;top:73px;width:448px;height:407px;border-radius:18px;background:linear-gradient(135deg,#e9f0f8,#7aa5d4 55%,#cfe0f0);box-shadow:12px 12px 0 var(--blue)}
.caps{top:1295px;height:615px;background:var(--tint)}
.card{background:#fff;border:1px solid var(--line);border-radius:16px}
.cap{top:202px;width:306px;height:325px;box-shadow:0 5px 0 var(--blue);text-align:center}
.cap .ic{width:86px;height:86px;border-radius:50%;background:var(--teal);margin:21px auto 0;display:flex;align-items:center;justify-content:center}
.cap h3{font-size:18px;margin-top:22px}
.cap p{font-size:14px;line-height:26px;color:var(--body);margin:12px 24px 0;height:104px;overflow:hidden}
.cap a,.post a{font-style:italic;font-size:13px;color:#333;text-decoration:underline}
.cap a{display:block;margin-top:10px}
.chars{top:1910px;height:527px}
.ch{top:200px;width:234px;height:242px;text-align:center}
.ch svg{margin-top:38px}
.ch p{font-size:14px;line-height:26px;color:#222;margin:18px 20px 0}
.cta{top:2437px;height:395px;background:linear-gradient(120deg,#0a4fa8,#0a63c0 50%,#0850a8)}
.cta .label,.cta .title{color:#fff}
.cta p{top:196px;font-size:14px;line-height:26px;color:#fff}
.insights{top:2832px;height:686px}
.post{top:190px;width:306px;height:403px;overflow:hidden}
.post .pic{height:225px}
.post h3{font-size:18px;line-height:26px;margin:22px 22px 0;font-weight:600}
.post p{font-size:13px;line-height:26px;color:var(--body);margin:10px 22px 4px;height:52px;overflow:hidden}
.post a{margin-left:22px}
.footer{top:3518px;height:336px;background:var(--blue);color:#fff}
.footer .brand{color:#fff;left:110px;top:110px}
.fcol{top:90px;font-size:14px}
.fcol h4{font-family:"Jura",sans-serif;font-size:16px;font-weight:600;margin-bottom:12px}
.fcol li{list-style:none;line-height:34px;display:flex;gap:12px;align-items:center}
.fcol li::before{content:"";width:7px;height:7px;border-radius:50%;background:#fff}
.contact div{display:flex;gap:10px;line-height:24px;margin-bottom:12px;font-size:14px}
.contact span.d{width:16px;height:16px;border-radius:50%;background:#fff;flex:none;margin-top:4px}
.social{left:110px;top:216px;display:flex;gap:12px}
.social i{width:22px;height:22px;border-radius:50%;background:#fff;display:block}
.rule{left:110px;top:282px;width:980px;height:1px;background:rgba(255,255,255,.35)}
.legal{left:110px;top:300px;font-size:14px}
.copy{left:820px;top:302px;font-size:14px}
</style>
</head>
<body>
<header class="site-header">
  <div class="abs brand"><i></i>QP FIDUCIARY</div>
  <nav class="abs nav"><span class="on">Home</span><span>Platform</span><span>Solutions</span><span>Insights</span><span>Company</span><span>Contact</span></nav>
  <svg class="abs" style="left:1060px;top:30px" width="22" height="24" viewBox="0 0 22 24"><circle cx="11" cy="7" r="6" fill="#0a5fd0"/><path d="M0 24c0-7 5-10 11-10s11 3 11 10z" fill="#0a5fd0"/></svg>
</header>

<section class="hero">
  <div class="abs hero-art" role="img" aria-label="Glowing layered platform of translucent tiles on a pale blue background"></div>
  <h1 class="abs center h">ACTUARIAL SOFTWARE FOR STRUCTURED,<br>AUDITABLE FINANCIAL ANALYSIS</h1>
  <p class="abs center">Software that translates actuarial methodologies into disciplined<br>decision-ready analytical tools across diverse regulatory environments.</p>
  <div class="abs btn" style="left:444px;top:271px;width:310px">Request a Technical Walkthrough</div>
</section>

<section class="overview">
  <div class="abs label" style="left:110px;top:88px">PLATFORM OVERVIEW</div>
  <h2 class="abs h title" style="left:110px;top:126px;line-height:48px">A Smarter Platform for<br>Modern Actuarial Workflows</h2>
  <p class="abs">QP Fiduciary delivers modular actuarial software built to support the full lifecycle of actuarial work — from reserving and valuation to pricing and risk analysis. Designed for flexibility, the platform adapts to diverse regulatory frameworks and evolving business needs, helping actuarial teams streamline complex calculations, improve transparency, and maintain consistency across models. Its modular structure allows organizations to implement the capabilities they need today while easily expanding as requirements grow.</p>
  <div class="abs btn" style="left:110px;top:480px;width:138px">Read More</div>
  <div class="abs ov-img" role="img" aria-label="Cluster of translucent blue cubes"></div>
</section>

<section class="caps">
  <div class="abs center label" style="top:36px">CORE SOLUTIONS</div>
  <h2 class="abs center h title" style="top:122px">Platform Capabilities</h2>
  <div class="abs card cap" style="left:110px">
    <div class="ic"><svg width="44" height="44" viewBox="0 0 44 44" fill="none" stroke="#fff" stroke-width="2"><rect x="8" y="6" width="24" height="32" rx="2"/><circle cx="20" cy="18" r="6"/><path d="M12 30h16M34 12l4 4-10 12h-4v-4z"/></svg></div>
    <h3 class="h">Reserving &amp; Valuation</h3>
    <p>Support structured reserving processes and financial reporting with software designed for accuracy, transparency, and regulatory</p>
    <a>Read More</a>
  </div>
  <div class="abs card cap" style="left:446px">
    <div class="ic"><svg width="44" height="44" viewBox="0 0 44 44" fill="none" stroke="#fff" stroke-width="2"><circle cx="26" cy="14" r="8"/><path d="M26 9v10M6 36l8-10h8l6-4 4 3-10 9H14"/></svg></div>
    <h3 class="h">Pricing</h3>
    <p>Develop robust pricing strategies with actuarial models tailored for both insurance and reinsurance products. The solution supports advanced data</p>
    <a>Read More</a>
  </div>
  <div class="abs card cap" style="left:782px">
    <div class="ic"><svg width="44" height="44" viewBox="0 0 44 44" fill="none" stroke="#fff" stroke-width="2"><rect x="6" y="8" width="20" height="30"/><path d="M10 14h4M18 14h4M10 20h4M18 20h4M10 26h4"/><circle cx="32" cy="22" r="5"/><path d="M24 38l8-10 8 10z"/></svg></div>
    <h3 class="h">Enterprise Risk Management</h3>
    <p>Strengthen risk oversight with tools designed for reinsurance optimization and capital modeling. The solution helps organizations evaluate risk</p>
    <a>Read More</a>
  </div>
</section>

<section class="chars">
  <div class="abs center label" style="top:80px">PLATFORM CHARACTERISTICS</div>
  <h2 class="abs center h title" style="top:120px">What Makes the Platform Different</h2>
  <div class="abs card ch" style="left:110px">
    <svg width="56" height="56" viewBox="0 0 56 56" fill="#0a9e86"><rect x="2" y="20" width="14" height="14" rx="2"/><rect x="38" y="2" width="14" height="14" rx="2"/><rect x="38" y="38" width="14" height="14" rx="2"/><path d="M16 25h10V9h12v4H30v12h8v4h-8v16h8v4H26V29H16z"/></svg>
    <p>Structured workflows suitable for multi-jurisdictional review</p>
  </div>
  <div class="abs card ch" style="left:360px">
    <svg width="56" height="56" viewBox="0 0 56 56"><circle cx="28" cy="24" r="14" fill="#0a9e86"/><path d="M21 24l5 5 9-9" stroke="#fff" stroke-width="3" fill="none"/><rect x="22" y="40" width="12" height="4" fill="#0a9e86"/><rect x="24" y="46" width="8" height="4" fill="#0a9e86"/><path d="M6 24h5M45 24h5M12 8l4 4M44 8l-4 4M28 2v5" stroke="#0a9e86" stroke-width="3"/></svg>
    <p>Transparent assumptions and methodological clarity</p>
  </div>
  <div class="abs card ch" style="left:608px">
    <svg width="66" height="56" viewBox="0 0 66 56" fill="none" stroke="#0a9e86" stroke-width="3"><circle cx="26" cy="26" r="18"/><path d="M12 28l8-8 6 10 6-12 6 8M38 38l10 10M48 12l12-8"/></svg>
    <p>Comparative scenario analysis</p>
  </div>
  <div class="abs card ch" style="left:857px">
    <svg width="56" height="56" viewBox="0 0 56 56" fill="none" stroke="#0a9e86" stroke-width="3"><circle cx="28" cy="26" r="10"/><path d="M23 26l4 4 6-7M28 4v6M28 42v6M6 26h6M44 26h6M12 10l4 4M44 10l-4 4M18 52h20"/></svg>
    <p>Supports professional judgment rather than replacing it</p>
  </div>
</section>

<section class="cta">
  <div class="abs center label" style="top:90px">REQUEST A DEMO</div>
  <h2 class="abs center h title" style="top:124px">Explore the Platform in Action</h2>
  <p class="abs center">See how QP Fiduciary's actuarial software can support your reserving, valuation, pricing, and risk analysis workflows. Our team can<br>guide you through the platform's capabilities, demonstrate real use cases, and answer your technical questions.</p>
  <div class="abs btn" style="left:446px;top:264px;width:308px">Request a Technical Walkthrough</div>
</section>

<section class="insights">
  <div class="abs center label" style="top:86px">INSIGHTS</div>
  <h2 class="abs center h title" style="top:122px">Industry Perspectives</h2>
  <div class="abs card post" style="left:110px">
    <div class="pic" role="img" aria-label="Abstract grey geometric mesh structure" style="background:linear-gradient(135deg,#6f7378,#c9cdd2 55%,#eef0f2)"></div>
    <h3 class="h">Advancing Approaches in Actuarial Reserving</h3>
    <p>A closer look at how actuarial reserving practices continue to evolve. This article</p>
    <a>Read More</a>
  </div>
  <div class="abs card post" style="left:446px">
    <div class="pic" role="img" aria-label="Deep blue abstract geometric background" style="background:linear-gradient(135deg,#1c7fcf,#0a4a9a 60%,#072f6e)"></div>
    <h3 class="h">Strengthening Governance in Cross-Border Analysis</h3>
    <p>Working across multiple regulatory environments requires disciplined</p>
    <a>Read More</a>
  </div>
  <div class="abs card post" style="left:782px">
    <div class="pic" role="img" aria-label="Pale glass blocks in soft light" style="background:linear-gradient(135deg,#f4f6f8,#d8dde3 50%,#eef1f4)"></div>
    <h3 class="h">Actuarial Challenges in Emerging Insurance Markets</h3>
    <p>Emerging markets bring new opportunities but also unique analytical</p>
    <a>Read More</a>
  </div>
</section>

<footer class="footer">
  <div class="abs brand"><i></i>QP FIDUCIARY</div>
  <div class="abs social"><i></i><i></i></div>
  <div class="abs fcol" style="left:443px"><h4>Quick Links</h4><ul><li>Company</li><li>Platform</li><li>Solutions</li><li>Insights</li></ul></div>
  <div class="abs fcol" style="left:607px"><h4>Platform</h4><ul><li>Platform Overview</li><li>Reserving &amp; Valuation</li><li>Pricing</li><li>Enterprise Risk Management</li></ul></div>
  <div class="abs fcol contact" style="left:885px"><h4>Contact Us</h4>
    <div><span class="d"></span><span>Suite 8, 210 Harbor Lane,<br>Brookfield, NY 10290</span></div>
    <div><span class="d"></span><span>info@qp-fiduciary.example</span></div>
    <div><span class="d"></span><span>+1 555 014 2318</span></div>
  </div>
  <div class="abs rule"></div>
  <div class="abs legal">Privacy Policy &nbsp;|&nbsp; Terms &amp; Conditions &nbsp;|&nbsp; Cookie Policy</div>
  <div class="abs copy">© 2026 QP Fiduciary. All rights reserved.</div>
</footer>
</body>
</html>
```